KVOR Individual and Corporate Development Business Card Design

KVOR needs a business card design that is aligned with it's values and targetted markets. Coherent Lattice of Adaptive Reasoning Method's self diagnosis model and tools, which can be used for personal improvement and team/business performance enhancement, is based on the learnings of over 20 years of medical practitioning. KVOR supercharges personal effectiveness and awareness to also increase team and business performance.

The targetted markets are high performance individuals and teams who aspire seek to enhance their capabilities and achieve their absolute best potential.

Look and feel for the business card design we are looking for is high technology, premium, fresh, new and medical.

Target Market(s)

Industry/Entity Type

Business Consultant

Contact Information for Business Card

Logo, Full Name, Title, Phone number, Email, company name, Address,

Font styles to use
Sans Serif

Requirements
Must have
• Tag line: Maximising Performance for Highly Effective People
• Please use same colours as the logo.

```html
<!DOCTYPE html>
<html lang="en">
<head>
<meta charset="utf-8">
<title>KVOR Business Card</title>
<link href="https://fonts.googleapis.com/css2?family=Michroma&family=Open+Sans:wght@400;600&display=swap" rel="stylesheet">
<style>
  :root {
    --teal: #00a8c6;
    --teal-deep: #1a9fb8;
    --ink: #151515;
    --paper: #ffffff;
    --muted: #d9d9d9;
    --rule: #555555;
    --backdrop: #e9e7e3;
  }
  * { box-sizing: border-box; margin: 0; padding: 0; }
  html, body { width: 1200px; height: 900px; overflow: hidden; }
  body { background: var(--backdrop); position: relative; font-family: "Open Sans", sans-serif; }

  .card {
    position: absolute;
    width: 600px;
    height: 343px;
    box-shadow: 0 10px 28px rgba(0,0,0,0.22);
  }

  /* Front: tagline */
  .card-front {
    left: 90px; top: 100px;
    background: var(--teal);
    display: flex; align-items: center; justify-content: center;
  }
  .tagline {
    font-family: "Michroma", sans-serif;
    color: var(--paper);
    text-transform: uppercase;
    text-align: center;
    line-height: 1.15;
    letter-spacing: 1px;
  }
  .tagline span { display: block; }
  .tagline .t-sm { font-size: 24px; }
  .tagline .t-md { font-size: 28px; }
  .tagline .t-lg { font-size: 44px; }

  /* Back: contact */
  .card-back {
    left: 510px; top: 450px;
    background: var(--ink);
    color: var(--paper);
  }
  .brand {
    position: absolute; right: 46px; top: 42px;
    text-align: left;
  }
  .brand-name {
    display: flex; align-items: center; gap: 12px;
    font-family: "Michroma", sans-serif;
    font-size: 46px; color: var(--teal);
    letter-spacing: 4px; line-height: 1;
  }
  .brand-dot { width: 14px; height: 14px; border-radius: 50%; background: var(--teal); }
  .brand-line {
    margin-top: 12px;
    font-family: "Michroma", sans-serif;
    font-size: 9px; color: var(--teal);
    text-transform: uppercase; letter-spacing: 0.5px;
    width: 250px; line-height: 1.4;
  }
  .brand-rule {
    position: absolute; right: 46px; top: 150px;
    width: 290px; height: 1px; background: var(--rule);
  }
  .person { position: absolute; left: 40px; top: 206px; }
  .person-name {
    font-family: "Michroma", sans-serif;
    font-size: 15px; color: var(--teal);
    text-transform: uppercase; letter-spacing: 1px;
  }
  .person-title { font-size: 14px; color: var(--muted); margin-top: 2px; }
  .name-rule {
    position: absolute; left: 250px; top: 222px;
    width: 130px; height: 1px; background: var(--rule);
  }
  .address {
    position: absolute; right: 40px; top: 198px;
    text-align: right; font-size: 13px; color: var(--muted); line-height: 1.5;
  }
  .contacts { position: absolute; left: 40px; top: 262px; list-style: none; }
  .contacts li {
    display: flex; align-items: center; gap: 8px;
    font-size: 14.5px; color: var(--muted); line-height: 1.45;
  }
  .contacts svg { width: 12px; height: 12px; fill: var(--teal); flex: none; }
</style>
</head>
<body>

  <section class="card card-front">
    <h1 class="tagline">
      <span class="t-md">Maximising</span>
      <span class="t-sm">Performance</span>
      <span class="t-md">For Highly</span>
      <span class="t-md">Effective</span>
      <span class="t-lg">People</span>
    </h1>
  </section>

  <section class="card card-back">
    <div class="brand">
      <div class="brand-name"><span class="brand-dot"></span>KVOR</div>
      <p class="brand-line">Coherent Lattice of Adaptive Reasoning Method</p>
    </div>
    <div class="brand-rule"></div>

    <div class="person">
      <p class="person-name">Daniel Mercer</p>
      <p class="person-title">Managing Director</p>
    </div>
    <div class="name-rule"></div>

    <p class="address">5678, Harbour Lane,<br>Westland, 54321</p>

    <ul class="contacts">
      <li>
        <svg viewBox="0 0 24 24" aria-hidden="true"><path d="M6.6 10.8a15.1 15.1 0 0 0 6.6 6.6l2.2-2.2c.3-.3.7-.4 1-.2 1.1.4 2.3.6 3.6.6.6 0 1 .4 1 1V20c0 .6-.4 1-1 1A17 17 0 0 1 3 4c0-.6.4-1 1-1h3.5c.6 0 1 .4 1 1 0 1.3.2 2.5.6 3.6.1.3 0 .7-.2 1z"/></svg>
        (044)987650432
      </li>
      <li>
        <svg viewBox="0 0 24 24" aria-hidden="true"><path d="M2 5h20v14H2z M4 7v.5l8 5 8-5V7l-8 5z" fill-rule="evenodd"/></svg>
        hello@kvor-mail.com
      </li>
      <li>
        <svg viewBox="0 0 24 24" aria-hidden="true"><path d="M12 2a10 10 0 1 0 0 20 10 10 0 0 0 0-20zm0 2c.9 1.2 1.6 2.6 2 4h-4c.4-1.4 1.1-2.8 2-4zM4.3 14a8 8 0 0 1 0-4h3.3a16 16 0 0 0 0 4zm.9 2h2.9c.3 1.3.8 2.5 1.5 3.6A8 8 0 0 1 5.2 16zM8.1 8H5.2a8 8 0 0 1 4.4-3.6C8.9 5.5 8.4 6.7 8.1 8zM12 20c-.9-1.2-1.6-2.6-2-4h4c-.4 1.4-1.1 2.8-2 4zm2.3-6H9.7a14 14 0 0 1 0-4h4.6a14 14 0 0 1 0 4zm.1 5.6c.7-1.1 1.2-2.3 1.5-3.6h2.9a8 8 0 0 1-4.4 3.6zM16.4 14a16 16 0 0 0 0-4h3.3a8 8 0 0 1 0 4z"/></svg>
        www.kvor-site.com
      </li>
    </ul>
  </section>

</body>
</html>
```